Brand and Marketing Coach Needs PDF Designed

I have content that i need placed into a simple but great PDF design. The PDF is about the formula I use to build personal brands. This is geared towards entrepreneurs, experts, coaches, therapists, wellness practitioners, and indpendent business owners who serve to improve the lives of others.
The company name is changing from TorvelCast to Selling with the Village (I don't have that logo yet, so working backwards a bit. For now, the TorvelCast logo can be used.) My brand is NOT formal and corporate, but it's also not neon-pink and screaming at you. It's down to earth, hip, a bit modern but warm. It's about no BS and authenticity. The final deliverable should make the reader feel focused, smart, motivated and hopeful.

Target Market(s)

Conscious entrepreneurs and small business owners. this one is specifically for pharmacy entrepreneurs but this will be used for various audiences later.

Font styles to use
Sans Serif

Colors
eaf1f7
3377b5
6b449b
f37122
faa54b
f68e4e
ffc214

Requirements
Must have
• Modern design. colors that match logo - 4e5583 (i think that is the blue.) d65a40.
• Could have these colors as well: c6a254, 01bcc3
• But open to other colors
Nice to have
• I'd like to see some ways to make this PDF simple and readable, and eye-catching. I'd also like to use the uploaded ebooks for design ideas.
Should not have
• neon colors, clip art

```html
<!DOCTYPE html>
<html lang="en">
<head>
<meta charset="utf-8">
<title>Who This Is For — TorvelCast</title>
<link rel="stylesheet" href="https://fonts.googleapis.com/css2?family=Rajdhani:wght@500&family=Catamaran:wght@300;400;500&display=swap">
<style>
  :root {
    --purple: #6b449b;
    --ink: #1f1f24;
    --muted: #85858c;
    --navy: #4e5583;
    --paper: #ffffff;
  }
  * { margin: 0; padding: 0; box-sizing: border-box; }
  html, body { width: 1200px; height: 927px; overflow: hidden; background: var(--paper); }
  .page { position: relative; width: 1200px; height: 927px; background: var(--paper); }

  .section-title {
    position: absolute; left: 291px; top: 220px;
    font-family: "Rajdhani", sans-serif; font-weight: 500;
    font-size: 34px; letter-spacing: 0.5px; color: var(--purple);
  }
  .intro {
    position: absolute; left: 296px; top: 275px; width: 800px;
    font-family: "Catamaran", sans-serif; font-weight: 300;
    font-size: 16.2px; line-height: 21px; color: var(--muted);
    white-space: nowrap;
  }
  .intro p + p { margin-top: 22px; }
  .intro strong { font-weight: 500; color: var(--ink); }

  .callout {
    position: absolute; left: 282px; top: 493px; width: 795px; height: 68px;
    background: var(--purple); color: #fff;
    padding: 11px 14px 0;
    font-family: "Catamaran", sans-serif; font-weight: 400;
    font-size: 25px; line-height: 21px;
  }

  .footer-rule {
    position: absolute; left: 296px; top: 845px; width: 904px; height: 4px;
    background: var(--purple);
  }
  .brand-name {
    position: absolute; left: 56px; top: 824px;
    font-family: "Catamaran", sans-serif; font-weight: 500;
    font-size: 34px; line-height: 1; color: var(--navy);
  }
</style>
</head>
<body>
<main class="page">
  <h1 class="section-title">WHO THIS IS FOR</h1>

  <div class="intro">
    <p><strong>The Personal Brand Blueprint</strong> is for you if you're <strong>a pharmacy entrepreneur</strong> who is starting or already running a<br>business or practice. You may <strong>be moving a brick and mortar business online; creating a new business as a<br>coach, patient advocate or navigator; or developing a service that will help your peers or patients.</strong></p>
    <p>If you already have a business, you feel frustrated because you're not attracting your ideal clients – the type<br>of clients you know you're meant to serve. And you don't know how you'll continue to expand your business.</p>
    <p>If you're in start-up, you understand that now is the time to nail down the right brand image and messaging<br>so you can come out of the gate running, rather than wasting your precious time and money on tactics that<br>don't work.</p>
  </div>

  <div class="callout">Long story short, you're ready to step it up, get noticed, and grow your<br>client base.</div>

  <span class="brand-name">TorvelCast</span>
  <div class="footer-rule"></div>
</main>
</body>
</html>
```